Walk Beside The River

Business Card design

Target Market(s)

People who require support in the commnity

Industry/Entity Type

Mental Health Support

Contact Information for Business Card

Mental Health Support Rosalind Tavener walkbesidetheriver@mailcove.com.au 0481 637 092 PO Box 926 Wattlebank QLD 4612

Colors
6B429C
8869AF
B7A5CE
E3DAEB
F3F0F8

Requirements
Must have
• Logo & details listed above
Should not have
• No red or orange

```html
<!DOCTYPE html>
<html lang="en">
<head>
<meta charset="utf-8">
<title>Walk Beside The River – Business Card</title>
<link rel="stylesheet" href="https://fonts.googleapis.com/css2?family=Montserrat:wght@800&family=Open+Sans:wght@400;600&display=swap">
<style>
  :root {
    --stage: #232323;
    --card: #1f1e23;
    --yellow: #f2e530;
    --purple: #6b429c;
    --purple-light: #8869af;
    --white: #f3f0f8;
    --pattern-light: #8a8a8f;
    --pattern-dark: #1c1b20;
  }
  * { margin: 0; padding: 0; box-sizing: border-box; }
  html, body {
    width: 1200px; height: 780px; overflow: hidden;
    background: var(--stage);
  }
  .stage {
    position: relative; width: 1200px; height: 780px;
  }
  .card {
    position: absolute; top: 60px; width: 380px; height: 660px;
    background: var(--card);
    border-left: 5px solid var(--yellow);
    box-shadow: 0 14px 30px rgba(0,0,0,0.45);
    overflow: hidden;
  }
  .card--back { left: 190px; }
  .card--front { left: 630px; }

  .back-pattern {
    position: absolute; inset: 0;
    background: linear-gradient(135deg, var(--pattern-light) 0%, #4a4a50 22%, var(--pattern-dark) 50%, var(--pattern-dark) 100%);
  }

  .brand {
    position: absolute; top: 56px; left: 0; right: 0;
    display: flex; flex-direction: column; align-items: center; gap: 16px;
  }
  .brand__dot {
    width: 120px; height: 120px; border-radius: 50%;
    background: var(--purple);
  }
  .brand__name {
    font-family: "Open Sans", sans-serif; font-weight: 600;
    font-size: 16px; letter-spacing: 2px; text-transform: uppercase;
    color: var(--white);
  }

  .person {
    position: absolute; left: 40px; right: 30px; top: 360px;
  }
  .person__name {
    font-family: "Montserrat", sans-serif; font-weight: 800;
    font-size: 34px; line-height: 1.1; color: var(--yellow);
    white-space: nowrap;
  }
  .person__name .surname { color: var(--purple-light); }
  .person__role {
    font-family: "Open Sans", sans-serif; font-size: 16px;
    color: var(--white); margin-top: 4px; padding-left: 120px;
  }

  .details {
    position: absolute; left: 40px; right: 20px; top: 470px;
    font-family: "Open Sans", sans-serif; color: var(--white);
  }
  .details__service { font-size: 15px; line-height: 1.35; margin-bottom: 16px; }
  .contact { list-style: none; font-size: 13.5px; line-height: 1.3; }
  .contact li { display: flex; align-items: center; gap: 9px; margin-bottom: 7px; white-space: nowrap; }
  .contact svg { width: 16px; height: 16px; flex: none; }
</style>
</head>
<body>
<main class="stage">
  <section class="card card--back">
    <div class="back-pattern" role="img" aria-label="Decorative grid of small stars fading from silver at the top left into black"></div>
  </section>

  <section class="card card--front">
    <div class="brand">
      <div class="brand__dot"></div>
      <p class="brand__name">Walk Beside The River</p>
    </div>

    <div class="person">
      <h1 class="person__name">Mirela <span class="surname">Hanakova</span></h1>
      <p class="person__role">CEO/Director</p>
    </div>

    <div class="details">
      <p class="details__service">Mental Health Support<br>Rosalind Tavener</p>
      <ul class="contact">
        <li>
          <svg viewBox="0 0 24 24" aria-hidden="true"><path fill="var(--yellow)" d="M6.6 10.8a15.1 15.1 0 0 0 6.6 6.6l2.2-2.2a1 1 0 0 1 1-.25 11.4 11.4 0 0 0 3.6.57 1 1 0 0 1 1 1V20a1 1 0 0 1-1 1A17 17 0 0 1 3 4a1 1 0 0 1 1-1h3.5a1 1 0 0 1 1 1c0 1.25.2 2.45.57 3.57a1 1 0 0 1-.25 1z"/></svg>
          0481 637 092
        </li>
        <li>
          <svg viewBox="0 0 24 24" aria-hidden="true"><rect x="2.5" y="5" width="19" height="14" rx="1.5" fill="none" stroke="var(--yellow)" stroke-width="2"/><path d="M3 6l9 7 9-7" fill="none" stroke="var(--yellow)" stroke-width="2"/></svg>
          walkbesidetheriver@mailcove.com.au
        </li>
        <li>
          <svg viewBox="0 0 24 24" aria-hidden="true"><path fill="none" stroke="var(--yellow)" stroke-width="2" d="M12 21s-6.5-6.2-6.5-11a6.5 6.5 0 0 1 13 0c0 4.8-6.5 11-6.5 11z"/><circle cx="12" cy="10" r="2.3" fill="var(--yellow)"/></svg>
          PO Box 926 Wattlebank QLD 4612
        </li>
      </ul>
    </div>
  </section>
</main>
</body>
</html>
```